Ecard for facebook and Instagram postings

I need 4 ecards (don't know if that is what it is called) for Facebook and Instagram postings. My Logo and company name should be incorporated and also be square. I would like to be able to insert text as I need. Examples are:

https://www.plorvexa.com/photo.php?fbid=20262841672382489&set=a.20261729249182489.516031.71298967488&type=1&relevant_count=1

https://media-a-kpt.yy.plorvexacdn.net/hpics-bmk4/2345967_657092986477056_308792573_n.jpg

I don't necessarily need images on them, just the color scheme to my business cards and the logo and business name. But if you'd like to give it an interesting look, you can go ahead and play with it. My site is tornquillmentoring.com, if you'd like to see the style of it.

Thank you!!!
Updates

I just uploaded the logo in two variations.  Thank you!

Target Market(s)

Women 16-65

Industry/Entity Type

Business

Requirements
Must have
• Logo and business name
Should not have
• No white background. I have attached business card picture so you can have an idea of what I'd like.

```html
<!DOCTYPE html>
<html lang="en">
<head>
<meta charset="utf-8">
<title>Tornquill Mentoring Services – Quote Card</title>
<link href="https://fonts.googleapis.com/css2?family=Tinos:wght@400;700&display=swap" rel="stylesheet">
<style>
  :root {
    --bg: #fff6ec;
    --orange: #f7941d;
    --orange-soft: #fbd6a8;
    --ring-soft: #efc4c8;
    --red: #b8202f;
    --ink: #0d0d0d;
    --gray: #3a3a3a;
    --white: #ffffff;
  }
  html, body {
    margin: 0;
    padding: 0;
    width: 1200px;
    height: 1200px;
    overflow: hidden;
    background: var(--bg);
  }
  .card {
    position: relative;
    width: 1200px;
    height: 1200px;
    background: var(--bg);
    overflow: hidden;
    font-family: "Tinos", "Times New Roman", serif;
  }
  .band-top {
    position: absolute;
    left: 0; top: 0;
    width: 100%; height: 22px;
    background: var(--orange);
  }
  .band-bottom {
    position: absolute;
    left: 0; bottom: 0;
    width: 100%; height: 24px;
    background: var(--red);
  }
  .backdrop {
    position: absolute;
    left: 0; top: 0;
    width: 1200px; height: 1200px;
    filter: blur(7px);
  }
  .quote-mark {
    position: absolute;
    color: var(--red);
    font-weight: 700;
    font-size: 270px;
    line-height: 1;
  }
  .quote-mark--open { left: 68px; top: 118px; }
  .quote-mark--close { left: 950px; top: 818px; }
  .quote-text {
    position: absolute;
    left: 60px;
    top: 245px;
    width: 1080px;
    margin: 0;
    text-align: center;
    color: var(--ink);
    font-weight: 700;
    font-size: 106px;
    line-height: 122px;
  }
  .brand-name {
    position: absolute;
    left: 26px;
    top: 1008px;
    margin: 0;
    line-height: 1;
  }
  .brand-name__main {
    display: block;
    color: var(--red);
    font-weight: 700;
    font-size: 104px;
  }
  .brand-name__sub {
    display: block;
    margin-top: 10px;
    margin-left: 6px;
    color: var(--gray);
    font-weight: 400;
    font-size: 27px;
    letter-spacing: 6px;
  }
  .brand-dot {
    position: absolute;
    left: 1000px;
    top: 1030px;
    width: 126px;
    height: 126px;
  }
</style>
</head>
<body>
  <main class="card">
    <div class="band-top"></div>

    <svg class="backdrop" viewBox="0 0 1200 1200" aria-hidden="true">
      <circle cx="600" cy="575" r="567" fill="none" stroke="var(--ring-soft)" stroke-width="16"/>
      <circle cx="600" cy="575" r="500" fill="var(--orange-soft)"/>
    </svg>

    <span class="quote-mark quote-mark--open" aria-hidden="true">&ldquo;</span>

    <blockquote class="quote-text">
      Ignorance is the<br>
      curse of God;<br>
      knowledge is the<br>
      wing wherewith we<br>
      fly to heaven
    </blockquote>

    <span class="quote-mark quote-mark--close" aria-hidden="true">&rdquo;</span>

    <p class="brand-name">
      <span class="brand-name__main">Tornquill</span>
      <span class="brand-name__sub">MENTORING SERVICES</span>
    </p>

    <svg class="brand-dot" viewBox="0 0 126 126" aria-hidden="true">
      <circle cx="63" cy="63" r="60" fill="var(--orange)" stroke="var(--white)" stroke-width="4"/>
    </svg>

    <div class="band-bottom"></div>
  </main>
</body>
</html>
```